Create banner ads for a digital product that deletes personal information from the web

The context of the banners is general advertisement for our service.
Please provide us with a set of static and flash/gif banners in the following standard sizes for the theme you create:
160x600
300x250
300x600
320x250
336x280
728x90
Please see our website for logo (just our name) and theme ideas - please follow similar color/font schemes if possible. www.quillbranchdata.com
Our company is an online service that deletes personal information from the internet for our members (automated opt-outs and content removal). Our target audience is anyone who wishes to protect their personal information from being on the internet (i.e. prefer to fly under the internet radar, for example). This is a product for U.S. residents who value privacy and online reputation. We seek to provide members with control of what 300+ websites are sharing about them – removing names, addresses, ages, phone numbers, email addresses, children’s information, home/property value information etc.
Internet

```html
<!DOCTYPE html>
<html lang="en">
<head>
<meta charset="utf-8">
<title>QuillBranch – Free Scan Banner 300x600</title>
<link rel="stylesheet" href="https://fonts.googleapis.com/css2?family=Poppins:wght@600&display=swap">
<style>
  :root {
    --sky-top: #1c4f8f;
    --sky-mid: #4f8fc6;
    --sky-low: #a9cbe0;
    --horizon: #e9dcae;
    --grass-light: #b7d64a;
    --grass-mid: #7fb22c;
    --grass-deep: #4f8a1c;
    --headline-light: #ffffff;
    --headline-dark: #111111;
    --button-top: #7fd66a;
    --button-bottom: #2f9a3a;
    --button-edge: #24802d;
    --brand: #ffffff;
  }
  html, body {
    margin: 0;
    padding: 0;
    width: 1200px;
    height: 2400px;
    overflow: hidden;
    background: #ffffff;
  }
  .banner {
    position: relative;
    width: 1200px;
    height: 2400px;
    overflow: hidden;
    font-family: "Poppins", sans-serif;
  }
  .banner__scene {
    position: absolute;
    inset: 0;
    background: linear-gradient(
      to bottom,
      var(--sky-top) 0%,
      var(--sky-mid) 30%,
      var(--sky-low) 58%,
      var(--horizon) 70%,
      var(--grass-light) 73%,
      var(--grass-mid) 85%,
      var(--grass-deep) 100%
    );
  }
  .headline {
    position: absolute;
    top: 112px;
    left: 0;
    width: 100%;
    margin: 0;
    text-align: center;
    font-size: 100px;
    font-weight: 600;
    line-height: 114px;
    letter-spacing: -1px;
  }
  .headline__line {
    display: block;
  }
  .headline__line--light {
    color: var(--headline-light);
  }
  .headline__line--dark {
    color: var(--headline-dark);
  }
  .cta-button {
    position: absolute;
    left: 300px;
    top: 1992px;
    width: 600px;
    height: 196px;
    border-radius: 98px;
    background: linear-gradient(to bottom, var(--button-top), var(--button-bottom));
    border: 4px solid var(--button-edge);
    box-sizing: border-box;
    display: flex;
    align-items: center;
    justify-content: center;
    color: #ffffff;
    font-size: 58px;
    font-weight: 600;
    text-decoration: none;
  }
  .brand-name {
    position: absolute;
    left: 0;
    top: 2208px;
    width: 100%;
    text-align: center;
    color: var(--brand);
    font-size: 132px;
    font-weight: 600;
    line-height: 170px;
    letter-spacing: 2px;
  }
</style>
</head>
<body>
  <div class="banner">
    <div class="banner__scene" role="img" aria-label="Photo of a man in a white shirt standing in a green grass field with arms raised toward a bright sunlit blue sky with clouds"></div>

    <h1 class="headline">
      <span class="headline__line headline__line--light">See what others</span>
      <span class="headline__line headline__line--light">can find out</span>
      <span class="headline__line headline__line--light">about you</span>
      <span class="headline__line headline__line--light">online</span>
      <span class="headline__line headline__line--dark">with a</span>
      <span class="headline__line headline__line--dark">free scan</span>
    </h1>

    <a class="cta-button" href="#">Get Started Now!</a>

    <div class="brand-name">QuillBranch</div>
  </div>
</body>
</html>
```